BrindleStaffing Business Card Design

We are a staffing company finding positions for dedicated nurses and physicians.

Target Market(s)

Business Professionals

Industry/Entity Type

Staffing

Contact Information for Business Card

Gordon Pratley
Chairman
417 39th Avenue South
SAINT PETERSBURG FL 33712
813-555-4172 Mobile
813-555-8036 Fax
gpratley@brindlestaffing.com
www.brindlestaffing.com

Font styles to use
Sans Serif

Colors
fbee3e
f04a50
f37122

Requirements
Must have
• Logo Attached, see colors below. We'd like to see Yellow, Orange and Red.

```html
<!DOCTYPE html>
<html lang="en">
<head>
<meta charset="utf-8">
<title>BrindleStaffing Business Card</title>
<link href="https://fonts.googleapis.com/css2?family=Roboto:wght@400;500;700&display=swap" rel="stylesheet">
<style>
  :root {
    --page-bg: #d9d6d2;
    --corner-yellow: #fbee3e;
    --cross-light: #f2f0ec;
    --field-orange: #f37122;
    --field-red: #f04a50;
    --text-cream: #fff4e2;
    --name-cream: #fff0cc;
    --logo-ink: #f04a50;
  }
  * { margin: 0; padding: 0; box-sizing: border-box; }
  html, body {
    width: 1200px; height: 969px; overflow: hidden;
    background: var(--page-bg);
    font-family: "Roboto", Arial, sans-serif;
  }
  .card {
    position: absolute; left: 100px; top: 200px;
    width: 1000px; height: 569px;
    background: linear-gradient(160deg, var(--field-orange) 0%, #f25e3a 50%, var(--field-red) 100%);
    overflow: hidden;
    box-shadow: 0 10px 30px rgba(0,0,0,0.18);
  }
  .corner { position: absolute; left: 0; width: 191px; background: var(--corner-yellow); }
  .corner--top { top: 0; height: 191px; }
  .corner--bottom { top: 375px; height: 194px; }
  .cross-bar { position: absolute; background: var(--cross-light); }
  .cross-bar--vertical { left: 191px; top: 0; width: 186px; height: 569px; }
  .cross-bar--horizontal { left: 0; top: 191px; width: 569px; height: 184px; }
  .brand-name {
    position: absolute; left: 70px; top: 247px;
    font-size: 60px; line-height: 72px; font-weight: 700; letter-spacing: -0.5px;
    color: var(--logo-ink); white-space: nowrap;
  }
  .details {
    position: absolute; right: 61px; text-align: right;
    color: var(--text-cream); font-size: 22px; line-height: 31px;
  }
  .address { top: 52px; }
  .contact { top: 420px; }
  .divider {
    position: absolute; right: 61px; width: 50px; height: 2px;
    background: var(--text-cream);
  }
  .divider--upper { top: 191px; }
  .divider--lower { top: 373px; }
  .person { position: absolute; right: 61px; top: 248px; text-align: right; }
  .person-name { font-size: 36px; font-weight: 700; color: var(--name-cream); line-height: 42px; }
  .person-title { font-size: 22px; font-weight: 500; color: var(--text-cream); line-height: 30px; }
</style>
</head>
<body>
  <div class="card">
    <div class="corner corner--top"></div>
    <div class="corner corner--bottom"></div>
    <div class="cross-bar cross-bar--vertical"></div>
    <div class="cross-bar cross-bar--horizontal"></div>

    <div class="brand-name">BrindleStaffing</div>

    <div class="details address">
      <p>417 39th Avenue South</p>
      <p>SAINT PETERSBURG FL 33712</p>
      <p>www.brindlestaffing.com</p>
    </div>

    <div class="divider divider--upper"></div>

    <div class="person">
      <p class="person-name">Gordon Pratley</p>
      <p class="person-title">Chairman</p>
    </div>

    <div class="divider divider--lower"></div>

    <div class="details contact">
      <p>(C) 813-555-4172</p>
      <p>(F) 813-555-8036</p>
      <p>gpratley@brindlestaffing.com</p>
    </div>
  </div>
</body>
</html>
```